10-year customer thank you card

We want a greeting card that our sales reps can send to companies/customers who have been with our company for 10 or more years. We're a software company, our corporate color is blue but we also like green, orange, and purple. We'd like something rather minimal/simplistic for this card, perhaps building off our tree logo. We're really open to ideas for this one. You must use the template files that are uploaded. Copy included in 10 year thank you card file; the copy may change based on how it looks when laid out
Updates

I updated our brief. We'd prefer a sans serif font. I also uploaded a blank infographic image that includes more of our approved colors.

Industry/Entity Type

Software

Font styles to use
Sans Serif

```html
<!DOCTYPE html>
<html lang="en">
<head>
<meta charset="UTF-8">
<title>10 Years Thank You Card</title>
<link rel="stylesheet" href="https://fonts.googleapis.com/css2?family=Lato:wght@400;700&family=Great+Vibes&display=swap">
<style>
  :root {
    --card-white: #ffffff;
    --card-grey: #d3d3d3;
    --brand-green: #1f7a33;
    --ink-green: #1e6b2c;
    --art-light: #3fae4c;
    --art-dark: #17772a;
    --rule-grey: #bdbdbd;
  }
  * { margin: 0; padding: 0; box-sizing: border-box; }
  html, body {
    width: 872px;
    height: 1200px;
    overflow: hidden;
    background: var(--card-white);
  }
  .card {
    position: relative;
    width: 872px;
    height: 1200px;
    font-family: "Lato", Arial, sans-serif;
  }
  .card-back {
    position: absolute;
    inset: 0 0 600px 0;
    background: var(--card-white);
  }
  .back-header {
    position: absolute;
    top: 0;
    left: 0;
    right: 0;
    height: 74px;
    border-top: 9px solid var(--brand-green);
    border-bottom: 2px solid var(--rule-grey);
    display: flex;
    justify-content: space-between;
    align-items: center;
    padding: 0 30px;
  }
  .back-url,
  .back-wordmark {
    display: inline-block;
    transform: rotate(180deg);
    color: var(--ink-green);
  }
  .back-url { font-size: 18px; }
  .back-wordmark {
    font-size: 21px;
    font-weight: 700;
  }
  .card-front {
    position: absolute;
    top: 600px;
    left: 0;
    width: 872px;
    height: 600px;
    background: var(--card-grey);
  }
  .anniversary-badge {
    position: absolute;
    top: 45px;
    left: 630px;
    width: 198px;
    padding: 6px 0;
    border-top: 2px solid var(--ink-green);
    border-bottom: 2px solid var(--ink-green);
    text-align: center;
    font-size: 38px;
    letter-spacing: 1px;
    color: var(--ink-green);
    line-height: 1.1;
  }
  .tree-art {
    position: absolute;
    top: 106px;
    left: 328px;
    width: 218px;
    height: 297px;
    background: linear-gradient(180deg, var(--art-light), var(--art-dark));
  }
  .thank-you {
    position: absolute;
    top: 418px;
    left: 0;
    width: 872px;
    text-align: center;
    font-family: "Great Vibes", cursive;
    font-size: 90px;
    color: var(--ink-green);
    line-height: 1.1;
  }
</style>
</head>
<body>
  <div class="card">
    <section class="card-back">
      <header class="back-header">
        <span class="back-url">www.larchwood.com</span>
        <span class="back-wordmark">Larchwood Software</span>
      </header>
    </section>

    <section class="card-front">
      <div class="anniversary-badge">10 YEARS</div>
      <div class="tree-art" role="img" aria-label="Green stylised evergreen tree illustration"></div>
      <div class="thank-you">Thank You</div>
    </section>
  </div>
</body>
</html>
```